Boutique custom software development company needs new business card

Our nearly 20 year old custom software development company would like to better include the fact that we are now providing Bitcoin services. These new services are B2B include education (how to acquire and securely hold Bitcoin) and integrating Bitcoin payments into existing ecommerce sites or other existing systems. Please keep the card clean and simple. Attached is our current design and some other files. vextorial.com

Target Market(s)

businesses owners interested in long term relationship

Industry/Entity Type

Custom software development and Bitcoin

Contact Information for Business Card

Dale Parker, dale@vextorial.com, vextorial.com, (888) 555-VXTRL

Font styles to use
Other font styles liked:
• monospace

Requirements
Must have
• double-sided
Nice to have
• clean and simple
Should not have
• physical address

```html
<!DOCTYPE html>
<html lang="en">
<head>
<meta charset="utf-8">
<title>Vextorial business card, front and back</title>
<link href="https://fonts.googleapis.com/css2?family=Open+Sans:wght@400;600;700;800&display=swap" rel="stylesheet">
<style>
  :root {
    --brand-blue: #3b74b9;
    --brand-blue-deep: #2f5f9f;
    --brand-orange: #ee7d22;
    --card-white: #ffffff;
    --stage: #232323;
  }
  * { box-sizing: border-box; margin: 0; padding: 0; }
  html, body { width: 1200px; height: 936px; overflow: hidden; background: var(--stage); }
  body { font-family: "Open Sans", Arial, sans-serif; }

  .canvas {
    position: relative; width: 1200px; height: 936px;
    display: flex; flex-direction: column; align-items: center; justify-content: center; gap: 40px;
  }
  .card {
    position: relative; width: 700px; height: 400px;
    border-radius: 24px; overflow: hidden;
  }

  /* Front */
  .card-front { background: var(--card-white); }
  .front-shapes { position: absolute; inset: 0; }
  .name-tab {
    position: absolute; left: 0; top: 36px; width: 30px; height: 40px;
    background: var(--brand-orange);
  }
  .holder-name {
    position: absolute; left: 44px; top: 28px;
    font-size: 38px; font-weight: 800; letter-spacing: 0.5px;
    color: var(--brand-blue);
  }
  .holder-name .first { color: var(--brand-orange); }

  .wordmark {
    position: absolute; right: 40px; top: 112px; text-align: right;
    color: var(--brand-blue);
  }
  .wordmark-line { display: flex; align-items: center; justify-content: flex-end; gap: 12px; }
  .wordmark-mark { width: 34px; height: 34px; background: var(--brand-orange); }
  .wordmark-name { font-size: 56px; font-weight: 800; line-height: 1; letter-spacing: 1px; }
  .wordmark-tagline { font-size: 20px; font-weight: 400; margin-top: 6px; letter-spacing: -0.3px; }

  .contact {
    position: absolute; right: 40px; bottom: 30px;
    list-style: none; text-align: right; color: var(--card-white);
    font-size: 19px; line-height: 1.5;
  }
  .contact li { display: flex; align-items: center; justify-content: flex-end; gap: 10px; }
  .contact .icon { width: 20px; height: 20px; flex: none; }

  /* Back */
  .card-back { background: var(--brand-blue); }
  .back-pattern {
    position: absolute; inset: 0;
    background: linear-gradient(120deg, var(--brand-blue-deep) 0%, var(--brand-blue) 55%, #7f9fd0 100%);
  }
  .back-wordmark {
    position: absolute; left: 0; right: 0; top: 130px; text-align: center; color: var(--card-white);
  }
  .back-wordmark .wordmark-line { justify-content: center; }
  .services {
    margin-top: 26px; display: inline-block;
    font-size: 18px; font-weight: 600; letter-spacing: 0.3px;
    color: var(--card-white);
    border-top: 2px solid var(--brand-orange); padding-top: 10px;
  }
  .services .accent { color: var(--brand-orange); }
</style>
</head>
<body>
<main class="canvas">

  <section class="card card-front" aria-label="Card front">
    <svg class="front-shapes" viewBox="0 0 700 400" width="700" height="400" aria-hidden="true">
      <polygon points="0,108 210,108 210,205 0,205" fill="var(--brand-blue)"/>
      <polygon points="0,205 700,205 700,400 0,400" fill="var(--brand-blue)"/>
      <polygon points="236,108 250,108 112,400 98,400" fill="var(--card-white)"/>
      <rect x="0" y="200" width="248" height="8" fill="var(--card-white)"/>
    </svg>

    <div class="name-tab"></div>
    <h1 class="holder-name"><span class="first">Dale</span> Parker</h1>

    <div class="wordmark">
      <div class="wordmark-line">
        <span class="wordmark-mark"></span>
        <span class="wordmark-name">Vextorial</span>
      </div>
      <p class="wordmark-tagline">developer of custom applications</p>
    </div>

    <ul class="contact">
      <li>(888) 555-VXTRL
        <svg class="icon" viewBox="0 0 20 20" aria-hidden="true"><path d="M5 2 L8 2 L9 6 L7 8 C8 11 9 12 12 13 L14 11 L18 12 L18 15 C18 17 16 18 14 18 C8 17 3 12 2 6 C2 4 3 2 5 2 Z" fill="var(--brand-orange)"/></svg>
      </li>
      <li>vextorial.com
        <svg class="icon" viewBox="0 0 20 20" aria-hidden="true"><circle cx="10" cy="10" r="8" fill="none" stroke="var(--brand-orange)" stroke-width="2"/><ellipse cx="10" cy="10" rx="3.5" ry="8" fill="none" stroke="var(--brand-orange)" stroke-width="1.6"/><line x1="2" y1="10" x2="18" y2="10" stroke="var(--brand-orange)" stroke-width="1.6"/></svg>
      </li>
      <li>dale@vextorial.com
        <svg class="icon" viewBox="0 0 20 20" aria-hidden="true"><rect x="2" y="5" width="16" height="11" rx="1" fill="var(--brand-orange)"/><polyline points="2,5 10,11 18,5" fill="none" stroke="var(--card-white)" stroke-width="1.4"/></svg>
      </li>
    </ul>
  </section>

  <section class="card card-back" aria-label="Card back">
    <div class="back-pattern" role="img" aria-label="Faint repeated brand pattern across the blue background"></div>
    <div class="back-wordmark">
      <div class="wordmark-line">
        <span class="wordmark-mark"></span>
        <span class="wordmark-name">Vextorial</span>
      </div>
      <p class="wordmark-tagline">developer of custom applications</p>
      <p class="services">Custom software <span class="accent">·</span> Bitcoin education <span class="accent">·</span> Bitcoin payment integration</p>
    </div>
  </section>

</main>
</body>
</html>
```